Marlo Tidecrest SUP Boards

We are a 100% owned and operated Australian Stand Up Paddle Board company, specialising in online sales of Stand Up Paddle Board packages.

We want our website to have an ocean, sunset, beach warm feel.

We sell 4 packages and need to be able to edit content and upload a number of photos of each package for sale.

Customers will be able to email us to receive quotes on freight costs and then pay via CoinLark only. We will have a Chatterbox page and Swapnest adds that need to be linked to the website also.

Target Market(s)

Surfers and Stand up paddle boarders

Industry/Entity Type

It Company

Number of Pages Required

3 page

Requirements
Must have
• Link to CoinLark for payment
• Link to Chatterbox page
• Three tabs- Welcome page, SUP Boards and a Contact us page

```html
<!DOCTYPE html>
<html lang="en">
<head>
<meta charset="utf-8">
<title>Marlo Tidecrest SUP Boards</title>
<link rel="stylesheet" href="https://fonts.googleapis.com/css2?family=Jost:wght@300;400;500;600&display=swap">
<style>
:root{
  --orange:#e9891f;
  --orange-text:#ee8a1c;
  --yellow:#f8c21a;
  --white:#ffffff;
  --ink:#1c1c1c;
  --body:#222222;
}
*{margin:0;padding:0;box-sizing:border-box}
html,body{width:1127px;height:1200px;overflow:hidden}
body{position:relative;font-family:"Jost",sans-serif;color:var(--body);background:#d98a2a}
.backdrop{position:absolute;inset:0;
  background:
    radial-gradient(ellipse 300px 500px at 80px 300px,rgba(90,45,10,.55),transparent 70%),
    radial-gradient(ellipse 260px 300px at 1080px 1150px,rgba(90,45,10,.6),transparent 70%),
    radial-gradient(ellipse 400px 300px at 560px 1000px,rgba(255,230,150,.7),transparent 70%),
    linear-gradient(180deg,#b86a1e 0%,#e59a3a 35%,#f2b860 60%,#d48a38 85%,#8a4a18 100%);}
.site-header{position:absolute;left:0;top:0;width:1127px;height:102px;background:var(--orange)}
.brand{position:absolute;left:137px;top:36px;width:200px;height:54px;display:flex;flex-direction:column;justify-content:center}
.brand-name{font-size:21px;font-weight:600;color:var(--ink);line-height:1.1;display:flex;align-items:center;gap:6px}
.brand-dot{width:12px;height:12px;background:var(--yellow);border-radius:50%}
.brand-sub{font-size:8px;letter-spacing:9px;color:var(--ink);margin-left:12px;margin-top:4px}
.main-nav{position:absolute;top:56px;left:0;width:1127px}
.main-nav a{position:absolute;color:var(--white);text-decoration:none;font-weight:500;font-size:16px;letter-spacing:.3px;line-height:22px}
.nav-active{position:absolute;left:426px;top:98px;width:72px;height:4px;background:var(--yellow)}
.social{position:absolute;right:173px;top:134px;display:flex;gap:14px}
.social a{color:var(--white);font-size:12px;font-weight:500;text-decoration:none}
.hero{position:absolute;left:173px;top:174px;width:781px;height:426px;
  background:
    linear-gradient(180deg,transparent 70%,#3a1608 100%),
    radial-gradient(ellipse 260px 120px at 420px 400px,#ffd23a,transparent 70%),
    linear-gradient(180deg,#c95a1f 0%,#e56a22 40%,#f07a22 70%,#c2451a 100%)}
.hero-title{position:absolute;left:0;width:781px;text-align:center;color:var(--ink);font-weight:300;font-size:29px;top:160px}
.hero-sub{position:absolute;left:0;width:781px;text-align:center;color:var(--white);font-weight:300;font-size:56px;top:192px;letter-spacing:1px}
.dots span{position:absolute;top:374px;width:10px;height:10px;border-radius:50%;background:var(--white)}
.dots span.on{background:var(--yellow)}
.content{position:absolute;left:172px;top:600px;width:781px;height:517px;background:var(--white)}
.section-title{position:absolute;left:0;width:781px;text-align:center;font-weight:400;font-size:19px;color:var(--ink);letter-spacing:.2px}
.intro{position:absolute;left:14px;top:78px;width:753px;text-align:center;font-size:14px;line-height:24px;font-weight:400}
.package{position:absolute;top:255px;width:172px}
.package-photo{height:108px}
.package-name{margin-top:10px;color:var(--orange-text);font-weight:500;font-size:14.5px;letter-spacing:.3px;padding-left:2px}
.package-text{margin-top:14px;font-size:12px;line-height:16px;padding-left:2px}
.order{position:absolute;top:219px;width:75px;height:26px;background:var(--orange);color:var(--white);font-size:9.5px;font-weight:600;line-height:26px;text-align:center;text-decoration:none}
.site-footer{position:absolute;left:0;top:1136px;width:1127px;text-align:center;color:var(--white);font-size:13px}
.footer-nav a{color:var(--white);text-decoration:none;margin:0 12px}
.footer-nav .sep{opacity:.9}
.copyright{margin-top:6px}
</style>
</head>
<body>
<div class="backdrop" role="img" aria-label="Blurred tropical beach sunset with palm fronds"></div>

<header class="site-header">
  <div class="brand">
    <div class="brand-name"><span class="brand-dot"></span>Marlo Tidecrest</div>
    <div class="brand-sub">SUP BOARDS · AUSTRALIA</div>
  </div>
  <nav class="main-nav">
    <a href="#" style="left:440px">HOME</a>
    <a href="#" style="left:518px">ABOUT US</a>
    <a href="#" style="left:627px">SERVICES</a>
    <a href="#" style="left:732px">PACKAGES</a>
    <a href="#" style="left:844px">CONTACT US</a>
  </nav>
  <div class="nav-active"></div>
</header>

<div class="social">
  <a href="#">ReelCove</a>
  <a href="#">Chirpline</a>
  <a href="#">Chatterbox</a>
</div>

<section class="hero" role="img" aria-label="Orange sunset sky over silhouetted palm trees">
  <div class="hero-title">Marlo Tidecrest SUP Boards</div>
  <div class="hero-sub">AUSTRALIA</div>
  <div class="dots">
    <span class="on" style="left:352px"></span>
    <span style="left:374px"></span>
    <span style="left:394px"></span>
    <span style="left:417px"></span>
  </div>
</section>

<main class="content">
  <h1 class="section-title" style="top:42px">WELCOME TO MARLO TIDECREST</h1>
  <p class="intro">orem Ipsum is simply dummy text of the printing and typesetting industry. Lorem Ipsum has been the industry's standard dummy text ever since the 1500s, when an unknown printer took a galley of type and scrambled it to make a type specimen book. . It has survived not only five centuries, but also the leap into electronic typesetting, remaining essentially unchanged. It was popularised in the 1960s with the release of Letraset sheets .</p>
  <h2 class="section-title" style="top:205px">PACKAGE FOR SALE</h2>

  <article class="package" style="left:13px">
    <div class="package-photo" role="img" aria-label="Paddler standing on a board in blue water" style="background:linear-gradient(180deg,#5b9fd6,#2e86c1 60%,#e8d890)"></div>
    <h3 class="package-name">PACKAGE 1</h3>
    <p class="package-text">Lorem Ipsum is simply dummy text of the printing and typesetting</p>
    <a class="order" href="#" style="left:0">ORDER NOW</a>
  </article>
  <article class="package" style="left:207px">
    <div class="package-photo" role="img" aria-label="Paddler on a board in a tropical turquoise lagoon" style="background:linear-gradient(180deg,#3a78c0,#7fb2d8 45%,#5cc7b4 60%,#9fe0cf)"></div>
    <h3 class="package-name">PACKAGE 2</h3>
    <p class="package-text">Lorem Ipsum is simply dummy text of the printing and typesetting</p>
    <a class="order" href="#" style="left:0">ORDER NOW</a>
  </article>
  <article class="package" style="left:404px">
    <div class="package-photo" role="img" aria-label="Paddler on a board on a lake with hills" style="background:linear-gradient(180deg,#5f86b5,#a9b9c7 50%,#8a7e6a 62%,#34577c)"></div>
    <h3 class="package-name">PACKAGE 3</h3>
    <p class="package-text">Lorem Ipsum is simply dummy text of the printing and typesetting</p>
    <a class="order" href="#" style="left:0">ORDER NOW</a>
  </article>
  <article class="package" style="left:598px">
    <div class="package-photo" role="img" aria-label="Paddler racing a board through river water" style="background:linear-gradient(180deg,#9aa88a,#6f8068 45%,#8fa7b8 70%,#d8e2e8)"></div>
    <h3 class="package-name">PACKAGE 4</h3>
    <p class="package-text">Lorem Ipsum is simply dummy text of the printing and typesetting</p>
    <a class="order" href="#" style="left:2px">ORDER NOW</a>
  </article>
</main>

<footer class="site-footer">
  <nav class="footer-nav">
    <a href="#">Home</a><span class="sep">|</span><a href="#">About Us</a><span class="sep">|</span><a href="#">Services</a><span class="sep">|</span><a href="#">Packages</a><span class="sep">|</span><a href="#">Contact Us</a>
  </nav>
  <p class="copyright">© 2014&nbsp; Company Name , All Right&nbsp; Reserved</p>
</footer>
</body>
</html>
```